New Bicycle shop business card

Hi!
I'm looking for a business card for my new proffesional bike mechanics shop. This shop is only for fixing broken bikes and not selling bikes.
Peferbly a modern and sleek and modern design.
Colors: black, grey, red, white
Information:
Name: Rijwielwerkplaats Vanhoutte
Shop owner: Bart Vanhoutte & Marieke Segers
Website: www.rijwielwerkplaats-vanhoutte.be
Email: info@rijwielwerkplaats-vanhoutte.be
Phone number: +32471902368
Street adres: Kerkweg 46
9940 Bellebeke
Slogan/shop information: Herstellingen van alle merken.
Logo: see files.
Target Market(s)
People who seek a mechanic to fix or upgrade their bikes.
Contact Information for Business Card
Information:
Website: info@rijwielwerkplaats-vanhoutte.be
9940 Bellebeke
Logo: see files.

```html
<!DOCTYPE html>
<html lang="nl">
<head>
<meta charset="utf-8">
<title>Rijwielwerkplaats Vanhoutte – Business Card</title>
<link rel="stylesheet" href="https://fonts.googleapis.com/css2?family=Open+Sans:wght@400;600;700;800&display=swap">
<style>
  :root {
    --bg: #5b5b5f;
    --bg-dark: #2a2a2c;
    --card: #060608;
    --red: #e8284a;
    --white: #ffffff;
    --grey: #a9abab;
  }
  * { margin: 0; padding: 0; box-sizing: border-box; }
  html, body {
    width: 1200px; height: 1000px; overflow: hidden;
    background: radial-gradient(ellipse at 50% 20%, var(--bg) 0%, var(--bg-dark) 100%);
    font-family: "Open Sans", sans-serif;
    color: var(--white);
  }
  .canvas {
    position: relative; width: 1200px; height: 1000px;
  }
  .card {
    position: absolute; left: 220px;
    width: 760px; height: 434px;
    background: var(--card);
    border-radius: 22px;
    box-shadow: 0 18px 40px rgba(0,0,0,.45);
  }
  .card--front { top: 46px; }
  .card--back { top: 520px; }

  .brand {
    display: flex; align-items: center; gap: 18px;
  }
  .brand__mark {
    width: 46px; height: 46px; border-radius: 50%;
    background: var(--red); flex: none;
  }
  .brand__name {
    font-weight: 800; color: var(--white);
    text-transform: uppercase; line-height: 1.05;
    letter-spacing: .04em;
  }

  .card--front .brand {
    position: absolute; left: 0; right: 0; top: 150px;
    justify-content: center;
  }
  .card--front .brand__name { font-size: 34px; }
  .card--front .brand__mark { width: 60px; height: 60px; }
  .tagline {
    position: absolute; left: 0; right: 0; top: 300px;
    text-align: center; font-size: 16px; font-weight: 600;
    letter-spacing: .03em;
  }

  .card--back .brand {
    position: absolute; left: 46px; top: 186px;
  }
  .card--back .brand__name { font-size: 24px; }

  .details {
    position: absolute; right: 44px; top: 44px;
    text-align: right;
  }
  .details__label { color: var(--red); font-size: 17px; font-weight: 600; }
  .details__owners { font-size: 19px; font-weight: 800; margin-top: 2px; }
  .details__company { color: var(--red); font-size: 20px; font-weight: 800; margin-top: 20px; }
  .details__role { font-size: 15px; font-weight: 700; margin-top: 2px; }
  .contact { list-style: none; margin-top: 18px; }
  .contact__item {
    display: flex; justify-content: flex-end; align-items: center; gap: 10px;
    font-size: 15px; line-height: 1.55;
  }
  .contact__icon { width: 15px; height: 15px; fill: var(--red); flex: none; }
  .details__address-label { color: var(--red); font-size: 17px; margin-top: 18px; }
  .details__address { font-size: 16px; margin-top: 2px; }
</style>
</head>
<body>
<main class="canvas">

  <section class="card card--front" aria-label="Voorzijde visitekaartje">
    <div class="brand">
      <span class="brand__mark"></span>
      <p class="brand__name">Rijwielwerkplaats<br>Vanhoutte</p>
    </div>
    <p class="tagline">Herstellingen van alle merken.</p>
  </section>

  <section class="card card--back" aria-label="Achterzijde visitekaartje">
    <div class="brand">
      <span class="brand__mark"></span>
      <p class="brand__name">Rijwielwerkplaats<br>Vanhoutte</p>
    </div>

    <div class="details">
      <p class="details__label">Shop owner:</p>
      <p class="details__owners">Bart Vanhoutte &amp; Marieke Segers</p>
      <p class="details__company">Rijwielwerkplaats Vanhoutte</p>
      <p class="details__role">General Manager</p>

      <ul class="contact">
        <li class="contact__item">+32471902368
          <svg class="contact__icon" viewBox="0 0 24 24" aria-hidden="true"><path d="M6.6 10.8a15.1 15.1 0 0 0 6.6 6.6l2.2-2.2a1 1 0 0 1 1-.25 11.4 11.4 0 0 0 3.6.57 1 1 0 0 1 1 1V20a1 1 0 0 1-1 1A17 17 0 0 1 3 4a1 1 0 0 1 1-1h3.5a1 1 0 0 1 1 1c0 1.25.2 2.45.57 3.57a1 1 0 0 1-.25 1z"/></svg>
        </li>
        <li class="contact__item">info@rijwielwerkplaats-vanhoutte.be
          <svg class="contact__icon" viewBox="0 0 24 24" aria-hidden="true"><path d="M2 5h20v14H2zm2 2v.5l8 5 8-5V7zm0 2.8V17h16V9.8l-8 5z"/></svg>
        </li>
        <li class="contact__item">www.rijwielwerkplaats-vanhoutte.be
          <svg class="contact__icon" viewBox="0 0 24 24" aria-hidden="true"><path d="M12 2a10 10 0 1 0 0 20 10 10 0 0 0 0-20zm6.9 6h-3a15 15 0 0 0-1.3-3.9A8 8 0 0 1 18.9 8zM12 4c.9 1.2 1.6 2.6 2 4h-4c.4-1.4 1.1-2.8 2-4zM4.3 14a8 8 0 0 1 0-4h3.4a16 16 0 0 0 0 4zm.8 2h3a15 15 0 0 0 1.3 3.9A8 8 0 0 1 5.1 16zm3-8h-3a8 8 0 0 1 4.3-3.9A15 15 0 0 0 8.1 8zM12 20c-.9-1.2-1.6-2.6-2-4h4c-.4 1.4-1.1 2.8-2 4zm2.3-6H9.7a14 14 0 0 1 0-4h4.6a14 14 0 0 1 0 4zm.3 5.9a15 15 0 0 0 1.3-3.9h3a8 8 0 0 1-4.3 3.9zm1.7-5.9a16 16 0 0 0 0-4h3.4a8 8 0 0 1 0 4z"/></svg>
        </li>
      </ul>

      <p class="details__address-label">Address</p>
      <p class="details__address">Kerkweg 46 9940 Bellebeke</p>
    </div>
  </section>

</main>
</body>
</html>
```